Oil Field Service company needs professional business cards

Looking to clean up our current company business cards and look a little more professional. Brenwick Casing Services is a US based company that services the oil field. We deal with engineers, managers and oil rigs....................................................................................................................................................................................................................................................................................................................................................................................................

Target Market(s)

Oil and Gas professionals

Industry/Entity Type

Oil And Gas

Contact Information for Business Card

See attached photo as example

Font styles to use
Sans Serif

Colors
ec1f27

Requirements
Must have
• Company Logo, Name, Title, Cell, Office, Fax, Email.
• See attached photo
Nice to have
• External CRT, Internal CRT, Casing Crews, Torque Turn, Laydown Machine
Should not have
• Do not introduce any new pictures and keep it professional looking

```html
<!DOCTYPE html>
<html lang="en">
<head>
<meta charset="utf-8">
<title>Brenwick Casing Services – Business Card</title>
<link rel="stylesheet" href="https://fonts.googleapis.com/css2?family=Open+Sans:ital,wght@0,400;0,600;0,700;1,400&display=swap">
<style>
  :root {
    --brand-red: #ec1f27;
    --card-black: #1c1c1d;
    --card-white: #f7f7f5;
    --steel: #4d5862;
    --steel-light: #6f7a84;
    --ink: #1e1e1e;
    --stage: #e8e6e2;
  }
  * { margin: 0; padding: 0; box-sizing: border-box; }
  html, body {
    width: 1200px; height: 775px; overflow: hidden;
    background: var(--stage);
    font-family: "Open Sans", Arial, sans-serif;
  }
  .sheet {
    width: 1200px; height: 775px;
    display: flex; align-items: center; justify-content: center; gap: 40px;
  }
  .card {
    width: 520px; height: 297px;
    border-radius: 4px;
    position: relative;
    box-shadow: 0 6px 18px rgba(0,0,0,.18);
  }

  /* Front */
  .card--front { background: var(--card-black); }
  .front-brand {
    position: absolute; left: 0; right: 0; top: 88px;
    display: flex; align-items: center; justify-content: center; gap: 14px;
  }
  .brand-mark { width: 16px; height: 16px; background: var(--brand-red); flex: none; }
  .brand-name {
    font-weight: 700; text-transform: uppercase; letter-spacing: 1px; line-height: 1.1;
  }
  .card--front .brand-name { color: var(--steel); font-size: 34px; }
  .services {
    position: absolute; left: 0; right: 0; bottom: 34px;
    text-align: center; color: var(--steel-light);
    font-size: 13px; letter-spacing: .5px;
  }
  .services .sep { margin: 0 8px; }

  /* Back */
  .card--back { background: var(--card-white); display: flex; align-items: center; }
  .back-brand {
    width: 215px; padding-left: 30px;
    display: flex; align-items: center; gap: 10px;
  }
  .card--back .brand-name { color: var(--steel); font-size: 19px; }
  .divider { width: 1px; height: 190px; background: var(--ink); margin: 0 26px 0 10px; }
  .contact { flex: 1; }
  .person { font-size: 21px; color: var(--ink); line-height: 1.1; }
  .person strong { font-weight: 700; }
  .role { font-style: italic; color: var(--brand-red); font-size: 14px; margin: 3px 0 14px; }
  .contact-list { list-style: none; }
  .contact-list li {
    display: flex; align-items: center; gap: 9px;
    font-size: 13px; color: var(--ink); line-height: 1; margin-bottom: 8px;
  }
  .icon { width: 13px; height: 13px; flex: none; }
</style>
</head>
<body>
<main class="sheet">
  <section class="card card--front" aria-label="Card front">
    <div class="front-brand">
      <span class="brand-mark"></span>
      <span class="brand-name">Brenwick<br>Casing Services</span>
    </div>
    <p class="services">Laydown Machine<span class="sep">|</span>Casing Crew<span class="sep">|</span>Mud Tool<span class="sep">|</span>Torque Turn</p>
  </section>

  <section class="card card--back" aria-label="Card back">
    <div class="back-brand">
      <span class="brand-mark"></span>
      <span class="brand-name">Brenwick<br>Casing Services</span>
    </div>
    <div class="divider"></div>
    <div class="contact">
      <p class="person">Cole <strong>Harlan</strong></p>
      <p class="role">Area Manager</p>
      <ul class="contact-list">
        <li>
          <svg class="icon" viewBox="0 0 14 14"><rect width="14" height="14" rx="2" fill="#ec1f27"/><path d="M4 3.5h2l1 2-1.2.9a5 5 0 0 0 1.8 1.8L8.5 7l2 1v2c0 .5-.4.8-.9.8A6.6 6.6 0 0 1 3.2 4.4c0-.5.3-.9.8-.9z" fill="#fff"/></svg>
          555 214-0700
        </li>
        <li>
          <svg class="icon" viewBox="0 0 14 14"><rect width="14" height="14" rx="2" fill="#ec1f27"/><rect x="4.5" y="2.5" width="5" height="9" rx="1" fill="none" stroke="#fff" stroke-width="1.2"/><circle cx="7" cy="9.8" r=".6" fill="#fff"/></svg>
          555 318-4427
        </li>
        <li>
          <svg class="icon" viewBox="0 0 14 14"><rect width="14" height="14" rx="2" fill="#ec1f27"/><rect x="3" y="6" width="8" height="5" rx="1" fill="#fff"/><rect x="4.5" y="3" width="5" height="3" fill="none" stroke="#fff" stroke-width="1"/></svg>
          555 214-0730
        </li>
        <li>
          <svg class="icon" viewBox="0 0 14 14"><rect width="14" height="14" rx="2" fill="#ec1f27"/><path d="M7 2.5a3 3 0 0 1 3 3c0 2.2-3 5.8-3 5.8S4 7.7 4 5.5a3 3 0 0 1 3-3z" fill="#fff"/><circle cx="7" cy="5.5" r="1" fill="#ec1f27"/></svg>
          Redmont, OK 73990
        </li>
        <li>
          <svg class="icon" viewBox="0 0 14 14"><rect width="14" height="14" rx="2" fill="#ec1f27"/><rect x="3" y="4" width="8" height="6" fill="#fff"/><path d="M3 4l4 3.2L11 4" fill="none" stroke="#ec1f27" stroke-width="1"/></svg>
          cole@brenwickcasing.com
        </li>
      </ul>
    </div>
  </section>
</main>
</body>
</html>
```